VOMRA Pty Ltd Business Card

Looking for a simple yet eye-catching double-sided business card design using my company logo on one side and contact details on the other.

Target Market(s)

Government

Industry/Entity Type

Communication Systems Engineering

Contact Information for Business Card

VOMRA Pty Ltd

Requirements
Nice to have
• Would be great to have a QR code so details can be scanned into contacts

```html
<!DOCTYPE html>
<html lang="en">
<head>
<meta charset="utf-8">
<title>VOMRA Pty Ltd Business Card</title>
<link href="https://fonts.googleapis.com/css2?family=Montserrat:wght@400;500;600;700&display=swap" rel="stylesheet">
<style>
  :root {
    --backdrop: #3b3b3b;
    --card-light: #ffffff;
    --card-light-shade: #f1f1f1;
    --ink: #2e3b43;
    --ink-soft: #4a555b;
    --rule: #c4c4c4;
    --card-dark-top: #2f4148;
    --card-dark-bottom: #1f2d33;
    --silver: #c9cccd;
  }
  * { margin: 0; padding: 0; box-sizing: border-box; }
  html, body {
    width: 1200px; height: 1200px; overflow: hidden;
    background: var(--backdrop);
    font-family: "Montserrat", sans-serif;
  }
  .stage {
    width: 1200px; height: 1200px;
    display: flex; flex-direction: column; align-items: center; justify-content: center;
    gap: 60px;
  }
  .card {
    position: relative;
    width: 860px; height: 491px;
    border-radius: 34px;
    overflow: hidden;
    box-shadow: 0 10px 30px rgba(0,0,0,.45);
  }
  /* Front: contact side */
  .card--front {
    background: linear-gradient(180deg, var(--card-light) 60%, var(--card-light-shade));
    color: var(--ink);
  }
  .brand {
    position: absolute; display: flex; align-items: center; gap: 22px;
  }
  .brand__dot { border-radius: 50%; flex: none; }
  .brand__name { font-weight: 600; letter-spacing: .06em; line-height: 1; }
  .card--front .brand { left: 230px; top: 80px; }
  .card--front .brand__dot { width: 86px; height: 86px; background: var(--ink); }
  .card--front .brand__name { font-size: 92px; color: var(--ink); }

  .person { position: absolute; left: 70px; top: 262px; }
  .person__name { font-size: 34px; font-weight: 700; letter-spacing: -.01em; line-height: 1; }
  .person__role { font-size: 19px; font-weight: 400; color: var(--ink-soft); margin-top: 4px; letter-spacing: .02em; }

  .divider {
    position: absolute; left: 70px; right: 70px; top: 340px;
    height: 2px; background: var(--rule);
  }
  .contacts {
    position: absolute; top: 362px; display: flex; flex-direction: column; gap: 10px;
    font-size: 24px; font-weight: 400; color: var(--ink);
  }
  .contacts--left { left: 95px; }
  .contacts--right { left: 470px; }
  .contact { display: flex; align-items: flex-start; gap: 14px; line-height: 1.15; }
  .contact svg { width: 28px; height: 28px; flex: none; fill: var(--ink); margin-top: 1px; }

  /* Back: brand side */
  .card--back {
    background: linear-gradient(160deg, var(--card-dark-top), var(--card-dark-bottom));
  }
  .card--back .brand { left: 50%; top: 50%; transform: translate(-50%, -50%); gap: 34px; }
  .card--back .brand__dot { width: 120px; height: 120px; background: var(--silver); }
  .card--back .brand__name { font-size: 118px; color: var(--silver); }
</style>
</head>
<body>
<main class="stage">
  <section class="card card--front" aria-label="Business card front">
    <div class="brand">
      <span class="brand__dot"></span>
      <span class="brand__name">VOMRA</span>
    </div>

    <div class="person">
      <p class="person__name">FULL NAME</p>
      <p class="person__role">POSITION</p>
    </div>

    <div class="divider"></div>

    <div class="contacts contacts--left">
      <p class="contact">
        <svg viewBox="0 0 24 24" aria-hidden="true"><path d="M6.6 10.8a15.1 15.1 0 0 0 6.6 6.6l2.2-2.2c.3-.3.7-.4 1-.2 1.1.4 2.3.6 3.6.6.6 0 1 .4 1 1V20c0 .6-.4 1-1 1A17 17 0 0 1 3 4c0-.6.4-1 1-1h3.5c.6 0 1 .4 1 1 0 1.3.2 2.5.6 3.6.1.3 0 .7-.2 1z"/></svg>
        (000) 000 0000
      </p>
      <p class="contact">
        <svg viewBox="0 0 24 24" aria-hidden="true"><path d="M2 5h20v14H2zm2 2v.4l8 5.2 8-5.2V7zm0 2.8V17h16V9.8l-8 5.2z"/></svg>
        admin@vomra.com.au
      </p>
    </div>

    <div class="contacts contacts--right">
      <p class="contact">
        <svg viewBox="0 0 24 24" aria-hidden="true"><path d="M12 2a10 10 0 1 0 0 20 10 10 0 0 0 0-20zm6.9 6h-3a15.6 15.6 0 0 0-1.3-3.6A8 8 0 0 1 18.9 8zM12 4c.8 1.2 1.5 2.5 1.9 4h-3.8c.4-1.5 1.1-2.8 1.9-4zM4.3 14a8 8 0 0 1 0-4h3.4a16 16 0 0 0 0 4zm.8 2h3a15.6 15.6 0 0 0 1.3 3.6A8 8 0 0 1 5.1 16zm3-8h-3a8 8 0 0 1 4.3-3.6C8.8 5.6 8.4 6.8 8.1 8zM12 20c-.8-1.2-1.5-2.5-1.9-4h3.8c-.4 1.5-1.1 2.8-1.9 4zm2.3-6H9.7a14 14 0 0 1 0-4h4.6a14 14 0 0 1 0 4zm.3 5.6c.6-1.1 1-2.3 1.3-3.6h3a8 8 0 0 1-4.3 3.6zm1.7-5.6a16 16 0 0 0 0-4h3.4a8 8 0 0 1 0 4z"/></svg>
        www.vomra.com.au
      </p>
      <p class="contact">
        <svg viewBox="0 0 24 24" aria-hidden="true"><path d="M12 2a7 7 0 0 0-7 7c0 5.2 7 13 7 13s7-7.8 7-13a7 7 0 0 0-7-7zm0 9.5a2.5 2.5 0 1 1 0-5 2.5 2.5 0 0 1 0 5z"/></svg>
        <span>45-47 Harlow St. Westmere<br>NSW 2150, Australia</span>
      </p>
    </div>
  </section>

  <section class="card card--back" aria-label="Business card back">
    <div class="brand">
      <span class="brand__dot"></span>
      <span class="brand__name">VOMRA</span>
    </div>
  </section>
</main>
</body>
</html>
```